Weightloss company needs Business Card

We want a business card that is clean and professional, yet portrays that we are a friendly, innovative, and versatile program designed to fit the needs of our clients.
I would like there to be 2 sides, one side having an appointment card, and the other side containing the logo and business information. There can be decorations on both sides. The logo is attached.

Target Market(s)

Men and women 40-60

Industry/Entity Type

Business

Contact Information for Business Card

Font styles to use
Sans Serif

Requirements
Must have
• The logo, space for business information
Nice to have
• The colors in the logo
Should not have
• No pictures of people or food

```html
<!DOCTYPE html>
<html lang="en">
<head>
<meta charset="utf-8">
<title>Renew Turn Wellness – Business Card</title>
<link rel="stylesheet" href="https://fonts.googleapis.com/css2?family=Open+Sans:wght@400;600;700;800&display=swap">
<style>
  :root {
    --brand-red: #e81e3a;
    --brand-blue: #45c8ef;
    --card-black: #050505;
    --card-white: #ffffff;
    --ink: #1a1a1a;
    --rule: #2a2a2a;
    --backdrop: #3a3a3c;
    --faint: #1c1c1c;
  }
  * { box-sizing: border-box; margin: 0; padding: 0; }
  html, body { width: 1200px; height: 900px; overflow: hidden; }
  body {
    background: var(--backdrop);
    font-family: "Open Sans", Arial, sans-serif;
    position: relative;
  }
  .card {
    position: absolute;
    width: 700px;
    height: 400px;
    border-radius: 26px;
    overflow: hidden;
    box-shadow: 0 14px 30px rgba(0,0,0,.45);
  }

  /* Appointment side */
  .card--appointment { left: 110px; top: 50px; background: var(--card-white); }
  .brand-name {
    position: absolute;
    font-weight: 800;
    color: var(--brand-red);
    letter-spacing: .5px;
    line-height: 1.05;
    display: flex; align-items: center; gap: 12px;
  }
  .brand-name .brand-dot {
    width: 22px; height: 22px; border-radius: 50%;
    background: var(--brand-blue); flex: none;
  }
  .card--appointment .brand-name { right: 60px; top: 58px; font-size: 30px; }
  .appointment-title {
    position: absolute; left: 60px; top: 205px;
    color: var(--brand-red); font-size: 17px; font-weight: 400; letter-spacing: .5px;
  }
  .appointment-field {
    position: absolute; left: 60px; right: 60px;
    display: flex; align-items: flex-end; gap: 10px;
    font-size: 17px; color: var(--ink);
  }
  .appointment-field .fill-line { flex: 1; border-bottom: 1.5px solid var(--rule); height: 18px; }
  .field-name { top: 245px; }
  .field-date { top: 292px; }
  .field-time { top: 339px; }

  /* Contact side */
  .card--contact { left: 390px; top: 450px; background: var(--card-black); }
  .backdrop-ring {
    position: absolute; left: 60px; top: 40px;
    width: 330px; height: 330px; border-radius: 50%;
    border: 22px solid var(--faint);
  }
  .person { position: absolute; left: 40px; top: 40px; }
  .person-name { color: var(--brand-red); font-size: 26px; font-weight: 400; letter-spacing: .5px; }
  .person-role { color: var(--brand-blue); font-size: 16px; font-weight: 600; letter-spacing: .5px; }
  .card--contact .brand-name { right: 50px; top: 70px; font-size: 30px; }
  .contact-list {
    position: absolute; right: 40px; top: 165px;
    list-style: none; color: #fff; font-size: 16px;
  }
  .contact-list li { display: flex; align-items: center; gap: 12px; margin-bottom: 6px; }
  .contact-list svg { width: 16px; height: 16px; flex: none; }
  .band { position: absolute; left: 0; bottom: 0; }
  .address {
    position: absolute; left: 40px; bottom: 18px;
    color: #fff; font-size: 17px; line-height: 1.3;
  }
</style>
</head>
<body>

<section class="card card--appointment" aria-label="Appointment side">
  <div class="brand-name"><span class="brand-dot"></span>Renew Turn<br>Wellness</div>
  <p class="appointment-title">APPOINTMENT</p>
  <div class="appointment-field field-name"><span>Name:</span><span class="fill-line"></span></div>
  <div class="appointment-field field-date"><span>Date:</span><span class="fill-line"></span></div>
  <div class="appointment-field field-time"><span>Time:</span><span class="fill-line"></span></div>
</section>

<section class="card card--contact" aria-label="Contact side">
  <div class="backdrop-ring"></div>
  <div class="person">
    <p class="person-name">MARCUS ELLERY</p>
    <p class="person-role">DIRECTOR</p>
  </div>
  <div class="brand-name"><span class="brand-dot"></span>Renew Turn<br>Wellness</div>
  <ul class="contact-list">
    <li>
      <svg viewBox="0 0 16 16"><path d="M3 1l3 3-1.5 2a9 9 0 005 5L11.5 9.5l3 3-2 2C6 14 2 10 1 3z" fill="var(--brand-red)"/></svg>
      +330 5512-0784
    </li>
    <li>
      <svg viewBox="0 0 16 16"><rect x="1" y="3" width="14" height="10" fill="none" stroke="var(--brand-red)" stroke-width="1.6"/><path d="M1 3l7 6 7-6" fill="none" stroke="var(--brand-red)" stroke-width="1.6"/></svg>
      info@renewturnwellness.com
    </li>
    <li>
      <svg viewBox="0 0 16 16"><circle cx="8" cy="8" r="6.5" fill="none" stroke="var(--brand-red)" stroke-width="1.6"/><ellipse cx="8" cy="8" rx="3" ry="6.5" fill="none" stroke="var(--brand-red)" stroke-width="1.2"/><path d="M1.5 8h13" stroke="var(--brand-red)" stroke-width="1.2"/></svg>
      www.renewturnwellness.com
    </li>
  </ul>
  <svg class="band" width="700" height="140" viewBox="0 0 700 140" aria-hidden="true">
    <polygon points="420,78 700,78 700,98 440,98" fill="var(--brand-blue)"/>
    <polygon points="0,70 300,70 440,140 0,140" fill="var(--brand-red)"/>
    <polygon points="300,70 400,70 480,110 440,140" fill="var(--brand-red)"/>
  </svg>
  <p class="address">Palm Avenue, 30512<br>Harbor City, Coastland</p>
</section>

</body>
</html>
```